Business card for my new company (Accounting firm)

I need a business card for my new business Brightwell Advisory and Ledger SA. Our services are accounting, tax, audit and financial management. Our customers are small companies, start-ups and new companies. The final design has to show financial security, trust and growth. Please find our logo attached to the business card. Text for the business card: Brightwell Advisory and Ledger SA Tomas Varenholt Director and Founder Certified Accountant Tel. 022 418 57 34 tv@clairevalconseil.ch www.clairevalconseil.ch Rue des Vergières 27 1201 Geneva
Target Market(s)
Our customers are small companies, start-ups and new companies.
Industry/Entity Type
Finance And Accounting
Contact Information for Business Card
Claireval Conseil et Comptes SA
Tomas Varenholt
Directeur et Fondateur
Expert-comptable diplômé
Tél. 022 418 57 34
tv@clairevalconseil.ch
www.clairevalconseil.ch
Rue des Vergières 27
1201 Genève

```html
<!DOCTYPE html>
<html lang="fr">
<head>
<meta charset="utf-8">
<title>Claireval Conseil et Comptes – cartes de visite</title>
<link href="https://fonts.googleapis.com/css2?family=Lato:wght@400;700;900&display=swap" rel="stylesheet">
<style>
  :root {
    --bg: #2b2b2d;
    --card: #ffffff;
    --card-shade: #eceef0;
    --blue: #2a9fd6;
    --blue-deep: #1b6fa8;
    --navy: #2f3d4c;
    --ink: #232629;
    --stripe: #3a3d42;
    --label: #2aa6e0;
  }
  * { margin: 0; padding: 0; box-sizing: border-box; }
  html, body { width: 1200px; height: 997px; overflow: hidden; }
  body {
    background: var(--bg);
    font-family: "Lato", Arial, sans-serif;
    position: relative;
  }
  .card {
    position: absolute;
    width: 560px;
    height: 320px;
    background: linear-gradient(160deg, var(--card) 55%, var(--card-shade));
    overflow: hidden;
    box-shadow: 0 10px 30px rgba(0,0,0,.45);
  }
  .card--back  { left: 60px;  top: 100px; }
  .card--front { left: 580px; top: 420px; }
  .card__band { position: absolute; inset: 0; width: 100%; height: 100%; }

  .logo {
    position: absolute;
    display: flex; align-items: center; gap: 10px;
    font-weight: 900; font-size: 17px; letter-spacing: 1.5px;
    text-transform: uppercase; color: var(--navy);
  }
  .logo__mark { width: 26px; height: 26px; background: var(--blue); }
  .card--front .logo { left: 40px; top: 72px; }
  .card--back  .logo { right: 36px; top: 60px; }

  .person { position: absolute; }
  .person__name { color: var(--blue); font-weight: 700; font-size: 16px; }
  .person__role { color: var(--ink); font-weight: 700; font-size: 13px; margin-top: 7px; }
  .card--front .person { right: 30px; top: 150px; text-align: right; }
  .card--front .person__name { border-bottom: 1.5px solid var(--blue-deep); padding: 0 0 4px 120px; }
  .card--back .person { left: 26px; top: 160px; }
  .card--back .person__name { font-size: 14px; }
  .card--back .person__role { font-size: 11px; font-weight: 400; margin-top: 3px; border-top: 1.5px solid var(--blue-deep); padding-top: 3px; width: 300px; }

  .contacts { position: absolute; list-style: none; font-size: 13px; color: var(--ink); }
  .contacts li { display: flex; align-items: center; gap: 7px; margin-bottom: 5px; }
  .contacts svg { width: 14px; height: 14px; flex: none; }
  .card--front .contacts { right: 36px; top: 214px; }
  .card--back .contacts { left: 26px; top: 218px; font-size: 12px; }

  .office { position: absolute; font-size: 14px; color: var(--ink); line-height: 1.2; }
  .office__name { color: var(--blue); font-weight: 700; }
  .card--front .office { left: 40px; top: 196px; border-top: 1.5px solid var(--blue-deep); padding-top: 8px; width: 280px; }
  .card--back .office { right: 36px; top: 150px; text-align: right; font-size: 12px; border-top: 1.5px solid var(--blue-deep); padding-top: 6px; width: 360px; }

  .web {
    position: absolute; color: #fff; font-weight: 900;
    font-size: 17px; letter-spacing: 2px;
  }
  .card--front .web { left: 44px; top: 285px; }
  .card--back .web { right: 30px; top: 285px; font-size: 15px; }

  .caption { position: absolute; color: var(--label); font-size: 19px; }
  .caption--back { left: 630px; top: 176px; }
  .caption--front { left: 744px; top: 760px; }
</style>
</head>
<body>

<section class="card card--back" lang="en">
  <svg class="card__band" viewBox="0 0 560 320" preserveAspectRatio="none" aria-hidden="true">
    <path d="M0 302 H200 C226 302 232 262 258 262 H560 V320 H0 Z" fill="var(--blue)"/>
    <path d="M0 289 H196 L190 295 H0 Z" fill="var(--stripe)"/>
  </svg>
  <div class="logo"><span class="logo__mark"></span>Claireval Conseil et Comptes</div>
  <div class="office">
    <div class="office__name">Brightwell Advisory and Ledger SA</div>
    <div>Rue des Vergières 27</div>
    <div>1201 Geneva</div>
  </div>
  <div class="person">
    <div class="person__name">Tomas Varenholt</div>
    <div class="person__role">Director/Founder Certified Accountant</div>
  </div>
  <ul class="contacts">
    <li><svg viewBox="0 0 14 14"><circle cx="7" cy="7" r="7" fill="var(--blue)"/><path d="M4 5.5c0-1 .8-1.5 3-1.5s3 .5 3 1.5L9 6.2 8.4 5.4H5.6L5 6.2Z M4.5 7.5h5v2.5h-5Z" fill="#fff"/></svg>022 418 57 34</li>
    <li><svg viewBox="0 0 14 14"><circle cx="7" cy="7" r="7" fill="var(--blue)"/><path d="M3.8 4.8h6.4v4.4H3.8Z M3.8 4.8 7 7.3 10.2 4.8" fill="none" stroke="#fff" stroke-width=".9"/></svg>tv@clairevalconseil.ch</li>
  </ul>
  <div class="web">www.clairevalconseil.ch</div>
</section>

<p class="caption caption--back">Back Card in English Language</p>

<section class="card card--front">
  <svg class="card__band" viewBox="0 0 560 320" preserveAspectRatio="none" aria-hidden="true">
    <path d="M0 255 H300 C322 255 328 272 350 272 H560 V320 H0 Z" fill="var(--blue)"/>
    <path d="M362 260 H560 V265 H360 Z" fill="var(--stripe)"/>
  </svg>
  <div class="logo"><span class="logo__mark"></span>Claireval Conseil et Comptes</div>
  <div class="person">
    <div class="person__name">Tomas Varenholt</div>
    <div class="person__role">Directeur et Fondateur Expert-comptable diplômé</div>
  </div>
  <ul class="contacts">
    <li><svg viewBox="0 0 14 14"><circle cx="7" cy="7" r="7" fill="var(--blue)"/><path d="M4 5.5c0-1 .8-1.5 3-1.5s3 .5 3 1.5L9 6.2 8.4 5.4H5.6L5 6.2Z M4.5 7.5h5v2.5h-5Z" fill="#fff"/></svg>022 418 57 34</li>
    <li><svg viewBox="0 0 14 14"><circle cx="7" cy="7" r="7" fill="var(--blue)"/><path d="M3.8 4.8h6.4v4.4H3.8Z M3.8 4.8 7 7.3 10.2 4.8" fill="none" stroke="#fff" stroke-width=".9"/></svg>tv@clairevalconseil.ch</li>
  </ul>
  <div class="office">
    <div class="office__name">Claireval Conseil et Comptes SA</div>
    <div>Rue des Vergières 27</div>
    <div>1201 Genève</div>
  </div>
  <div class="web">www.clairevalconseil.ch</div>
</section>

<p class="caption caption--front">Front Card in French Language</p>

</body>
</html>
```